Weightloss company needs Business Card

We want a business card that is clean and professional, yet portrays that we are a friendly, innovative, and versatile program designed to fit the needs of our clients.
I would like there to be 2 sides, one side having an appointment card, and the other side containing the logo and business information. There can be decorations on both sides. The logo is attached.

Target Market(s)

Men and women 40-60

Industry/Entity Type

Business

Contact Information for Business Card

Font styles to use
Sans Serif

Requirements
Must have
• The logo, space for business information
Nice to have
• The colors in the logo
Should not have
• No pictures of people or food

```html
<!DOCTYPE html>
<html lang="en">
<head>
<meta charset="utf-8">
<title>Turnway Weightloss – Business Card</title>
<link rel="stylesheet" href="https://fonts.googleapis.com/css2?family=Source+Sans+3:wght@400;600;700&display=swap">
<style>
  :root {
    --backdrop: #3b3430;
    --card-black: #050505;
    --card-glow: #1c1c1c;
    --brand-red: #f0163f;
    --brand-cyan: #25d2f2;
    --text-white: #f4f4f4;
    --ghost: #141414;
    --ghost-text: #0a0a0a;
  }
  * { box-sizing: border-box; margin: 0; padding: 0; }
  html, body { width: 1200px; height: 844px; overflow: hidden; }
  body {
    background: var(--backdrop);
    font-family: "Source Sans 3", Arial, sans-serif;
    position: relative;
  }
  .card {
    position: absolute;
    top: 267px;
    width: 540px;
    height: 310px;
    overflow: hidden;
    box-shadow: 0 14px 30px rgba(0,0,0,.45);
  }
  /* Contact side */
  .card--contact {
    left: 40px;
    background: linear-gradient(100deg, var(--card-black) 0%, #0d0d0d 60%, var(--card-glow) 100%);
  }
  .band { position: absolute; left: 0; width: 100%; }
  .band--top { top: 0; height: 14px; background: var(--brand-red); }
  .band--bottom { bottom: 0; height: 14px; background: var(--brand-cyan); }
  .ghost-mark {
    position: absolute;
    left: -110px; top: 40px;
    width: 260px; height: 260px;
    border-radius: 50%;
    background: var(--ghost);
  }
  .ghost-name {
    position: absolute;
    left: -20px; top: 130px;
    font-size: 58px; font-weight: 700;
    color: var(--ghost-text);
    line-height: 1;
    white-space: nowrap;
  }
  .person {
    position: absolute;
    left: 210px; top: 70px;
  }
  .person__name {
    font-size: 17px; font-weight: 600;
    letter-spacing: .5px;
    text-transform: uppercase;
    padding-bottom: 3px;
    border-bottom: 1px solid var(--brand-cyan);
  }
  .person__first { color: var(--brand-red); }
  .person__last { color: var(--brand-cyan); }
  .person__role {
    color: var(--text-white);
    font-size: 14px;
    margin-top: 3px;
    padding-left: 20px;
  }
  .contact {
    position: absolute;
    left: 150px; top: 160px;
    width: 300px;
    text-align: center;
    color: var(--text-white);
    font-size: 14px;
    line-height: 18px;
  }
  .contact__address {
    position: absolute;
    left: 0; right: 0; bottom: 30px;
    text-align: center;
    color: var(--text-white);
    font-size: 14px;
  }
  /* Logo side */
  .card--logo {
    left: 620px;
    background: radial-gradient(ellipse at 55% 40%, #262626 0%, var(--card-black) 65%);
  }
  .tab { position: absolute; width: 22px; height: 44px; }
  .tab--red { left: 0; bottom: 40px; background: var(--brand-red); }
  .tab--cyan { right: 0; top: 24px; background: var(--brand-cyan); }
  .brand {
    position: absolute;
    left: 0; right: 0; top: 130px;
    display: flex; align-items: center; justify-content: center; gap: 12px;
  }
  .brand__dot {
    width: 14px; height: 14px;
    border-radius: 50%;
    background: var(--brand-red);
  }
  .brand__name {
    color: var(--brand-red);
    font-size: 34px; font-weight: 700;
    line-height: 1;
  }
</style>
</head>
<body>
  <section class="card card--contact" aria-label="Contact side">
    <div class="band band--top"></div>
    <div class="ghost-mark"></div>
    <div class="ghost-name">Turnway</div>
    <div class="person">
      <p class="person__name"><span class="person__first">Daniel</span> <span class="person__last">Harper</span></p>
      <p class="person__role">Managing Director</p>
    </div>
    <div class="contact">
      <p>044-456-7890</p>
      <p>123-456-7890</p>
      <p>infoname@yourwebsite.com</p>
      <p>www.website.com</p>
    </div>
    <p class="contact__address">1234 Address Tag Line | Country Name, AB | 123456</p>
    <div class="band band--bottom"></div>
  </section>

  <section class="card card--logo" aria-label="Logo side">
    <div class="tab tab--cyan"></div>
    <div class="brand">
      <span class="brand__dot"></span>
      <span class="brand__name">Turnway Weightloss</span>
    </div>
    <div class="tab tab--red"></div>
  </section>
</body>
</html>
```